Tech business card design

We need an amazing business card design for our new business 'Pexla' a marketing tech startup based in Sydney, Australia. We provide an online marketplace for businesses to search and buy advertising media, connect with service providers and learn more about marketing. We wish to communicate 'cool tech', reliability and professionalism and design based around our logo.

Target Market(s)

Business Owners

Contact Information for Business Card

Name
Position
Email Address
Website
Phone Number

Font styles to use
Other font styles liked:
• Avenir & Avenir Next

Colors

Designer to choose colors to be used in the design.

```html
<!DOCTYPE html>
<html lang="en">
<head>
<meta charset="utf-8">
<title>Pexla business card</title>
<link rel="stylesheet" href="https://fonts.googleapis.com/css2?family=Open+Sans:wght@400;700;800&display=swap">
<style>
  :root {
    --backdrop: #a0cee2;
    --card-white: #ffffff;
    --navy: #11133a;
    --navy-text: #1c1f4a;
    --rule-blue: #1f2d6b;
    --edge-grey: #45464f;
    --body-grey: #3a3a3f;
    --pale-text: #d3d5e4;
  }
  * { margin: 0; padding: 0; box-sizing: border-box; }
  html, body { width: 1200px; height: 1184px; overflow: hidden; }
  body {
    position: relative;
    background: var(--backdrop);
    font-family: "Open Sans", Arial, sans-serif;
  }
  .card {
    position: absolute;
    left: 148px;
    width: 903px;
    height: 518px;
    border-radius: 38px;
    overflow: hidden;
  }
  .card-front { top: 46px; background: var(--card-white); }
  .card-back {
    top: 620px;
    background: var(--navy);
    border: 3px solid var(--edge-grey);
  }
  .front-band {
    position: absolute;
    left: 0; right: 0; bottom: 0;
    height: 37px;
    background: var(--navy);
    border: 3px solid var(--edge-grey);
    border-radius: 0 0 38px 38px;
  }
  .wordmark {
    position: absolute;
    font-weight: 800;
    font-size: 142px;
    line-height: 1;
    letter-spacing: -2px;
    white-space: nowrap;
  }
  .card-front .wordmark { left: 482px; top: 52px; color: var(--navy); }
  .card-back .wordmark { left: 0; right: 0; text-align: center; top: 190px; color: var(--card-white); }
  .accent-rule {
    position: absolute;
    left: 427px; right: 0; top: 263px;
    height: 3px;
    background: var(--rule-blue);
  }
  .contact { position: absolute; left: 72px; top: 233px; color: var(--body-grey); }
  .contact-name { font-size: 28px; font-weight: 700; color: var(--navy-text); line-height: 1; letter-spacing: -0.3px; }
  .contact-role { font-size: 25px; line-height: 1.05; color: var(--body-grey); }
  .contact-line {
    display: flex; align-items: center; gap: 10px;
    font-size: 22px; line-height: 1;
  }
  .contact-line svg { width: 22px; height: 22px; flex: none; fill: var(--navy-text); }
  .line-phone { margin-top: 16px; }
  .line-email { margin-top: 16px; }
  .line-web { margin-top: 12px; letter-spacing: 2.5px; }
  .contact-address { margin-top: 12px; font-size: 22px; line-height: 1.15; }
  .back-url {
    position: absolute; left: 0; right: 0; top: 420px;
    text-align: center;
    font-size: 30px;
    letter-spacing: 3.5px;
    color: var(--pale-text);
  }
</style>
</head>
<body>
  <section class="card card-front">
    <div class="wordmark">pexla</div>
    <div class="accent-rule"></div>
    <div class="contact">
      <div class="contact-name">JOHN SMITH</div>
      <div class="contact-role">Position</div>
      <div class="contact-line line-phone">
        <svg viewBox="0 0 24 24" aria-hidden="true"><circle cx="12" cy="12" r="10.5" fill="none" stroke="#1c1f4a" stroke-width="1.6"/><path d="M9 6.5c-1.5 1-2 3-1 5.5s3 4.5 5 5.5c1.2.5 2.3 0 3-1l-2-2-1.2.8c-1.3-.7-2.4-2-3-3.3l.9-1.1-1.7-4.4z"/></svg>
        <span>012-345-6789</span>
      </div>
      <div class="contact-line line-email">
        <svg viewBox="0 0 24 24" aria-hidden="true"><path d="M1 5h22v14H1z"/><path d="M2 6l10 8 10-8M2 18l7-6M22 18l-7-6" fill="none" stroke="#fff" stroke-width="1.6"/></svg>
        <span>info@pexla.com</span>
      </div>
      <div class="contact-line line-web">
        <svg viewBox="0 0 24 24" aria-hidden="true" fill="none" stroke="#1c1f4a" stroke-width="1.5"><circle cx="12" cy="12" r="10.5"/><ellipse cx="12" cy="12" rx="4.5" ry="10.5"/><path d="M1.5 12h21M3 7h18M3 17h18M12 1.5v21"/></svg>
        <span>www.pexla.com</span>
      </div>
      <div class="contact-address">Street name City Name,<br>Zipcode,012345</div>
    </div>
    <div class="front-band"></div>
  </section>

  <section class="card card-back">
    <div class="wordmark">pexla</div>
    <div class="back-url">www.pexla.com</div>
  </section>
</body>
</html>
```